Design for a real estate wev portal

Contents and features of the site
---------------------------------
Website in 5 languages: French, Dutch, English, German, Spanish.
English name of the site: Harbor Nest Place
Main purpose of the site:
- allow people to rent their house/ appartment for flatsharing purposes.
- help people wanting to find a room in flatsharing
- help people to find additional roommates for their flatsharing
Key interaction sequence:
1. I create a "group" of people who have common interest/hobbies
2. People who have the same interests/hobbies join my group
3. I look for a house/appartment to host my group
Website structure will be the following:
- Home
- Groups
-- Look for a group
--- Join a group
-- Create a group
- Properties
-- Look for a house/appartement
-- Apply
- Sales conditions
- Contact
- My account
-- My profile
-- My groups OR my properties
Your mission
------------
The client has no graphical guidelines, simply a logo (see attached).
We need a (responsive compliant) design for the following pages (we expect PSD's from you. No HTML nor CSS):
1. homepage (see example and wireframe attached)
2. properties search result list (see wireframe attached)
3. "detailed" form for properties
4. groups search result list
5. "detailed" form for groups
6. my account page
FOR THE COMPETITION step we only expect from you the design of first 2 screens.
Based on that, we will select the designer who will win the project, and will have to design the 4 remaining screens.
Target Market(s)
B2C
Industry/Entity Type
Real Estate
Number of Pages Required
5+ page
Look and feel
Each slider illustrates characteristics of the customer's brand and the style your logo design should communicate.

```html
<!DOCTYPE html>
<html lang="fr">
<head>
<meta charset="utf-8">
<title>Harbor Nest Place – Recherche de colocations</title>
<link rel="stylesheet" href="https://fonts.googleapis.com/css2?family=Dosis:wght@400;500;600;700&display=swap">
<style>
:root{
  --teal:#1a9fb1;
  --teal-dark:#138797;
  --green:#6cbf45;
  --ink:#3b3b3b;
  --text:#555;
  --muted:#888;
  --line:#dcdcdc;
  --soft:#f4f4f4;
  --sky-a:#a7d2dd;
  --sky-b:#cfe6ec;
}
*{box-sizing:border-box;margin:0;padding:0}
html,body{width:1155px;height:1200px;overflow:hidden;background:#fff}
body{position:relative;font-family:"Dosis",sans-serif;color:var(--text);font-size:10px}
.abs{position:absolute}
.topbar{left:0;top:0;width:1155px;height:3px;background:var(--green)}
.header{left:0;top:3px;width:1155px;height:125px;background:linear-gradient(100deg,var(--sky-a),var(--sky-b) 55%,#b9dbe4)}
.nav{left:236px;top:4px;width:200px;height:123px;background:var(--teal)}
.nav a{position:absolute;color:#fff;font-weight:600;font-size:10px;text-decoration:none;letter-spacing:.2px}
.nav a.active{border-bottom:1px solid #fff;padding-bottom:2px}
.dropdown{left:386px;top:116px;width:152px;height:50px;background:var(--green);z-index:3}
.dropdown:before{content:"";position:absolute;left:5px;top:-8px;border:4px solid transparent;border-bottom:8px solid var(--green);border-left-width:0}
.dropdown a{position:absolute;left:13px;color:#fff;font-weight:600;font-size:9.5px;text-decoration:none}
.dropdown .sep{position:absolute;left:13px;right:10px;top:24px;height:1px;background:rgba(255,255,255,.5)}
.brand{left:496px;top:40px;display:flex;align-items:center;gap:8px}
.brand .dot{width:14px;height:14px;border-radius:50%;background:var(--green)}
.brand span{font-size:25px;font-weight:600;color:#3a3a3a;letter-spacing:.5px}
.btn-outline,.btn-login{top:14px;height:21px;font-size:9.5px;font-weight:600;color:#fff;display:flex;align-items:center;justify-content:center}
.btn-outline{left:792px;width:78px;border:1px solid #fff}
.btn-login{left:875px;width:46px;background:var(--teal)}
.panel{border:1px solid #e6e6e6}
.sidebar{left:236px;top:146px;width:155px;height:812px}
.main{left:401px;top:146px;width:520px;height:812px}
.h-side{font-weight:600;font-size:11px;color:var(--ink)}
.label{font-size:9.5px;color:var(--text)}
.field{border:1px solid var(--line);font-size:9.5px;color:#666;display:flex;align-items:center;justify-content:center;background:#fff}
.radio{width:11px;height:11px;border-radius:50%;border:1px solid #cfcfcf;background:#f2f2f2}
.radio.on{background:radial-gradient(circle,var(--teal) 0 3px,#fff 3.5px)}
.card{left:418px;width:485px;height:165px;border:1px solid #e3e3e3;background:#fff}
.card .photo{position:absolute;left:15px;top:10px;width:218px;height:144px}
.card .price{position:absolute;left:11px;top:14px;width:65px;height:28px;background:var(--teal);color:#fff;font-size:15px;font-weight:500;display:flex;align-items:center;padding-left:8px}
.card .price small{font-size:7px;margin-top:5px}
.card .play{position:absolute;left:94px;top:52px;width:32px;height:32px;border:2px solid rgba(255,255,255,.9);border-radius:50%}
.card .title{position:absolute;left:247px;top:12px;font-size:15px;color:var(--ink);display:flex;align-items:center;gap:6px}
.card .tag{position:absolute;left:247px;top:38px;width:87px;height:20px;background:var(--teal);color:#fff;font-size:9.5px;display:flex;align-items:center;justify-content:center}
.card .upd{position:absolute;left:349px;top:42px;font-size:9.5px}
.card .meta{position:absolute;left:247px;top:67px;font-size:9px;font-style:italic;color:var(--muted)}
.card .meta span{margin-left:18px}
.card .lead{position:absolute;left:247px;top:94px;font-size:9.5px;font-weight:700;color:var(--ink)}
.card .desc{position:absolute;left:247px;top:109px;width:230px;font-size:9.5px;line-height:14.5px}
.card .icons{position:absolute;left:247px;top:144px;display:flex;gap:4px}
.footer{left:0;top:976px;width:1155px;height:221px;background:#f3f3f3}
.footer h4{position:absolute;top:47px;font-size:11.5px;font-weight:700;color:var(--ink)}
.footer p,.footer li{font-size:9px;line-height:16px;color:#555}
.footer ul{position:absolute;list-style:none;top:72px}
.footer li:before{content:"› ";}
.bottomline{left:235px;top:1156px;width:686px;height:1px;background:#aaa}
.copy{top:1166px;font-size:11px;color:#555}
.bottombar{left:0;top:1196px;width:1155px;height:4px;background:var(--green)}
</style>
</head>
<body>
<div class="abs topbar"></div>
<header class="abs header"></header>

<nav class="abs nav">
  <a style="left:21px;top:41px">HOME</a>
  <a style="left:97px;top:41px">SALES CONDITIONS</a>
  <a style="left:19px;top:67px">GROUPS ˅</a>
  <a style="left:97px;top:67px">CONTACT</a>
  <a style="left:19px;top:93px">PROPERTIES ˅</a>
  <a class="active" style="left:97px;top:93px">MY ACCOUNT ˅</a>
</nav>
<div class="abs dropdown">
  <a style="top:10px">MY PROFILE</a>
  <div class="sep"></div>
  <a style="top:29px">MY GROUPS OR MY PROPERTIES</a>
</div>

<div class="abs brand"><div class="dot"></div><span>Harbor Nest Place</span></div>
<div class="abs btn-outline">REGISTER HERE</div>
<div class="abs btn-login">LOGIN</div>

<aside class="abs panel sidebar"></aside>
<div class="abs h-side" style="left:246px;top:159px">VOTRE RECHERCHE:</div>
<div class="abs field" style="left:246px;top:181px;width:133px;height:24px;justify-content:flex-start;padding-left:10px;color:#aaa">
  <svg width="10" height="10" viewBox="0 0 10 10" style="margin-right:5px"><circle cx="4" cy="4" r="3" fill="none" stroke="#aaa"/><path d="M6.5 6.5L9 9" stroke="#aaa"/></svg>Ou cherchez-vous?
</div>
<div class="abs label" style="left:246px;top:225px">Perimetre de recherche:</div>
<div class="abs" style="left:246px;top:242px;width:130px;height:3px;background:#ddd"></div>
<div class="abs" style="left:246px;top:242px;width:82px;height:3px;background:var(--teal)"></div>
<svg class="abs" style="left:323px;top:243px" width="10" height="10" viewBox="0 0 10 10"><path d="M5 0v8M2 5l3 3 3-3" stroke="var(--teal)" stroke-width="1.5" fill="none"/></svg>
<div class="abs" style="left:317px;top:253px;font-size:9px;font-style:italic;color:var(--teal)">20km</div>

<div class="abs label" style="left:246px;top:279px">Loyer par mois</div>
<div class="abs field" style="left:246px;top:298px;width:78px;height:24px">Min</div>
<div class="abs field" style="left:329px;top:298px;width:51px;height:24px">500</div>

<div class="abs label" style="left:246px;top:337px">Type de logement</div>
<div class="abs field" style="left:246px;top:357px;width:66px;height:24px">Maison</div>
<div class="abs field" style="left:317px;top:357px;width:63px;height:24px">Appartement</div>

<div class="abs label" style="left:246px;top:394px">Chambres Disponibles</div>
<div class="abs field" style="left:246px;top:414px;width:28px;height:24px">1</div>
<div class="abs field" style="left:273px;top:414px;width:32px;height:24px">2</div>
<div class="abs field" style="left:304px;top:414px;width:35px;height:24px">3</div>
<div class="abs field" style="left:338px;top:414px;width:41px;height:24px">4</div>

<div class="abs radio on" style="left:248px;top:452px"></div><div class="abs label" style="left:266px;top:452px">Annonces avec photo</div>
<div class="abs radio" style="left:248px;top:472px"></div><div class="abs label" style="left:266px;top:472px">Chambres Doubles</div>
<div class="abs radio on" style="left:248px;top:492px"></div><div class="abs label" style="left:266px;top:492px">Meubles</div>
<div class="abs radio" style="left:248px;top:512px"></div><div class="abs label" style="left:266px;top:512px">Courte Duree</div>

<div class="abs label" style="left:246px;top:541px">Age du Colocatire</div>
<div class="abs field" style="left:246px;top:561px;width:78px;height:24px">35 ˅</div>
<div class="abs field" style="left:329px;top:561px;width:51px;height:24px">40 ˅</div>

<div class="abs label" style="left:246px;top:599px">Sexe du Colocataire</div>
<div class="abs field" style="left:246px;top:619px;width:67px;height:24px">Homme</div>
<div class="abs field" style="left:317px;top:619px;width:63px;height:24px">Femme</div>

<div class="abs label" style="left:246px;top:657px">Situation du Colocataire</div>
<div class="abs field" style="left:246px;top:677px;width:67px;height:24px">Edudiant</div>
<div class="abs field" style="left:317px;top:677px;width:63px;height:24px">Salarie</div>

<div class="abs" style="left:241px;top:726px;width:143px;height:3px;background:#e6e6e6"></div>
<svg class="abs" style="left:248px;top:748px" width="14" height="14" viewBox="0 0 14 14"><circle cx="7" cy="4.5" r="3.3" fill="none" stroke="#666"/><path d="M1 13.5c0-3.5 2.7-5.5 6-5.5s6 2 6 5.5z" fill="none" stroke="#666"/></svg>
<div class="abs h-side" style="left:269px;top:750px">MEMBRE BASIQUE</div>
<div class="abs" style="left:246px;top:776px;width:135px;font-size:9.5px;line-height:13.7px">Lorem ipsum dolor sit amet, consectetur adipisicing elit, sed do eiusmod tempor</div>
<div class="abs" style="left:246px;top:831px;width:135px;font-size:9.5px;line-height:13.7px">incididunt ut labore et dolore magna aliqua. Ut enim ad minim veniam, quis nostrud exercitation ullamco laboris nisi ut aliquip ex ea commodo</div>
<div class="abs" style="left:246px;top:911px;width:127px;height:31px;background:var(--teal);color:#fff;font-weight:700;font-size:11.5px;display:flex;align-items:center;justify-content:center">Activer un pass</div>

<section class="abs panel main"></section>
<div class="abs" style="left:419px;top:160px;font-size:11px;font-weight:600;color:var(--ink)">0 offres de colocation a paris-ile De France</div>
<div class="abs label" style="left:747px;top:162px">Trier par</div>
<div class="abs field" style="left:791px;top:155px;width:111px;height:25px;justify-content:space-between;padding:0 10px">Plus recent <span>˅</span></div>

<article class="abs card" style="top:198px">
  <div class="photo" role="img" aria-label="Photo d'un immeuble résidentiel sous un ciel bleu" style="background:linear-gradient(160deg,#3d6fb8,#8fb1d8 45%,#c9a25a 70%,#5c7a3c)"><div class="play"></div></div>
  <div class="price">€500<small>/Mois</small></div>
  <div class="title"><svg width="12" height="16" viewBox="0 0 12 16"><path d="M6 15S1 9 1 6a5 5 0 0110 0c0 3-5 9-5 9z" fill="none" stroke="#888"/><circle cx="6" cy="6" r="2" fill="none" stroke="#888"/></svg>Rue Des Tilleuls, Montre...</div>
  <div class="tag">Membre Premium</div><div class="upd">Mis a jour il y a 1 jour</div>
  <div class="meta">Disponible le 26 dec.<span>Non specifie</span></div>
  <div class="lead">Appartement loue meuble de 3ch, 100m2 a 5min a pie...</div>
  <div class="desc">Bonjour, Je propose a partir du mois de decembre mon appartement libre pour en faire une colocation meublee.Il</div>
  <div class="icons"><svg width="12" height="10" viewBox="0 0 12 10"><rect x=".5" y=".5" width="11" height="9" fill="none" stroke="#777"/><path d="M1 9l4-4 3 3 2-2 2 2" fill="none" stroke="#777"/></svg><svg width="11" height="10" viewBox="0 0 11 10"><path d="M.5 4.5L10.5.5 7 9.5 5 6z" fill="none" stroke="#777"/></svg></div>
</article>

<article class="abs card" style="top:371px">
  <div class="photo" role="img" aria-label="Photo d'une maison familiale avec pelouse et panneau à vendre" style="background:linear-gradient(180deg,#5f92c9,#a9c7e3 35%,#b98a4b 55%,#5d8a3a 75%,#4f7a30)"><div class="play"></div></div>
  <div class="price">€500<small>/Mois</small></div>
  <div class="title"><svg width="12" height="16" viewBox="0 0 12 16"><path d="M6 15S1 9 1 6a5 5 0 0110 0c0 3-5 9-5 9z" fill="none" stroke="#888"/><circle cx="6" cy="6" r="2" fill="none" stroke="#888"/></svg>Rue Des Tilleuls, Montre...</div>
  <div class="tag">Membre Premium</div><div class="upd">Mis a jour il y a 1 jour</div>
  <div class="meta">Disponible le 26 dec.<span>Non specifie</span></div>
  <div class="lead">Appartement loue meuble de 3ch, 100m2 a 5min a pie...</div>
  <div class="desc">Bonjour, Je propose a partir du mois de decembre mon appartement libre pour en faire une colocation meublee.Il</div>
  <div class="icons"><svg width="12" height="10" viewBox="0 0 12 10"><rect x=".5" y=".5" width="11" height="9" fill="none" stroke="#777"/><path d="M1 9l4-4 3 3 2-2 2 2" fill="none" stroke="#777"/></svg><svg width="11" height="10" viewBox="0 0 11 10"><path d="M.5 4.5L10.5.5 7 9.5 5 6z" fill="none" stroke="#777"/></svg></div>
</article>

<article class="abs card" style="top:544px">
  <div class="photo" role="img" aria-label="Photo d'une terrasse fleurie face à des tours de ville" style="background:linear-gradient(180deg,#e6e9ee,#b9c1cc 50%,#8a9099 70%,#c8442a 85%,#6b8a3a)"><div class="play"></div></div>
  <div class="price">€500<small>/Mois</small></div>
  <div class="title"><svg width="12" height="16" viewBox="0 0 12 16"><path d="M6 15S1 9 1 6a5 5 0 0110 0c0 3-5 9-5 9z" fill="none" stroke="#888"/><circle cx="6" cy="6" r="2" fill="none" stroke="#888"/></svg>Rue Des Tilleuls, Montre...</div>
  <div class="tag">Membre Premium</div><div class="upd">Mis a jour il y a 1 jour</div>
  <div class="meta">Disponible le 26 dec.<span>Non specifie</span></div>
  <div class="lead">Appartement loue meuble de 3ch, 100m2 a 5min a pie...</div>
  <div class="desc">Bonjour, Je propose a partir du mois de decembre mon appartement libre pour en faire une colocation meublee.Il</div>
  <div class="icons"><svg width="12" height="10" viewBox="0 0 12 10"><rect x=".5" y=".5" width="11" height="9" fill="none" stroke="#777"/><path d="M1 9l4-4 3 3 2-2 2 2" fill="none" stroke="#777"/></svg><svg width="11" height="10" viewBox="0 0 11 10"><path d="M.5 4.5L10.5.5 7 9.5 5 6z" fill="none" stroke="#777"/></svg></div>
</article>

<article class="abs card" style="top:716px">
  <div class="photo" role="img" aria-label="Photo d'une maison blanche avec grand panneau à vendre" style="background:linear-gradient(120deg,#7fa6d2,#dfe3e8 40%,#c9c2b4 60%,#c3282d 80%,#c3282d)"><div class="play"></div></div>
  <div class="price">€500<small>/Mois</small></div>
  <div class="title"><svg width="12" height="16" viewBox="0 0 12 16"><path d="M6 15S1 9 1 6a5 5 0 0110 0c0 3-5 9-5 9z" fill="none" stroke="#888"/><circle cx="6" cy="6" r="2" fill="none" stroke="#888"/></svg>Rue Des Tilleuls, Montre...</div>
  <div class="tag">Membre Premium</div><div class="upd">Mis a jour il y a 1 jour</div>
  <div class="meta">Disponible le 26 dec.<span>Non specifie</span></div>
  <div class="lead">Appartement loue meuble de 3ch, 100m2 a 5min a pie...</div>
  <div class="desc">Bonjour, Je propose a partir du mois de decembre mon appartement libre pour en faire une colocation meublee.Il</div>
  <div class="icons"><svg width="12" height="10" viewBox="0 0 12 10"><rect x=".5" y=".5" width="11" height="9" fill="none" stroke="#777"/><path d="M1 9l4-4 3 3 2-2 2 2" fill="none" stroke="#777"/></svg><svg width="11" height="10" viewBox="0 0 11 10"><path d="M.5 4.5L10.5.5 7 9.5 5 6z" fill="none" stroke="#777"/></svg></div>
</article>

<footer class="abs footer">
  <h4 style="left:235px">ABOUT REAL HOMES</h4>
  <p class="abs" style="left:238px;top:74px;width:195px">Lorem ipsum dolor sit amet, consectetur adipisicing elit, sed do eiusmod tempor incididunt ut labore et dolore magna aliqua. Ut enim ad minim veniam, quis nostrud exercitation ullamco laboris nisi ut aliquip ex ea commodo consequat.</p>
  <h4 style="left:466px">QUICK LINKS</h4>
  <ul style="left:466px;line-height:17px"><li>Single Family</li><li>New construction</li><li>On rent</li><li>On sale</li></ul>
  <ul style="left:550px;line-height:17px"><li>Single Family</li><li>New construction</li><li>On rent</li><li>On sale</li></ul>
  <h4 style="left:645px">LATEST INFO</h4>
  <ul style="left:645px;width:130px;line-height:12.5px"><li style="margin-bottom:5px">Lorem ipsum dolor sit amet, consectetur adipisicing</li><li style="margin-bottom:5px">Lorem ipsum dolor sit amet, consectetur</li><li>adipisicing elit, sed do eiusmod tempor incididunt</li></ul>
  <h4 style="left:798px">ADDRESS</h4>
  <svg class="abs" style="left:798px;top:76px" width="10" height="13" viewBox="0 0 12 16"><path d="M6 15S1 9 1 6a5 5 0 0110 0c0 3-5 9-5 9z" fill="none" stroke="#666"/><circle cx="6" cy="6" r="2" fill="none" stroke="#666"/></svg>
  <p class="abs" style="left:815px;top:74px;width:110px;line-height:14.5px">niam, quis nostrud exercitn lamco laboris nisi ut aliquip ex ea, London</p>
  <svg class="abs" style="left:795px;top:125px" width="15" height="10" viewBox="0 0 15 10"><rect x="3" y=".5" width="11" height="8" fill="none" stroke="#666"/><path d="M3 .5l5.5 4 5.5-4M0 3h2M0 6h2" fill="none" stroke="#666"/></svg>
  <p class="abs" style="left:815px;top:121px">contact@harbornest.example</p>
  <svg class="abs" style="left:797px;top:142px" width="12" height="12" viewBox="0 0 12 12"><circle cx="6" cy="6" r="5.5" fill="none" stroke="#666"/><path d="M4 3.5c0 2.5 1.5 4.5 4.5 5" fill="none" stroke="#666"/></svg>
  <p class="abs" style="left:815px;top:140px">+10200 3040 5060</p>
</footer>
<div class="abs bottomline"></div>
<div class="abs copy" style="left:235px">@All right reserved by the company 2015.</div>
<div class="abs copy" style="left:808px">Designed by Studio Larkspur</div>
<div class="abs bottombar"></div>
</body>
</html>
```